Weightloss company needs Business Card

We want a business card that is clean and professional, yet portrays that we are a friendly, innovative, and versatile program designed to fit the needs of our clients.
I would like there to be 2 sides, one side having an appointment card, and the other side containing the logo and business information. There can be decorations on both sides. The logo is attached.

Target Market(s)

Men and women 40-60

Industry/Entity Type

Business

Contact Information for Business Card

Font styles to use
Sans Serif

Requirements
Must have
• The logo, space for business information
Nice to have
• The colors in the logo
Should not have
• No pictures of people or food

```html
<!DOCTYPE html>
<html lang="en">
<head>
<meta charset="utf-8">
<title>Brightturn Weightloss – Business Card</title>
<link rel="stylesheet" href="https://fonts.googleapis.com/css2?family=Open+Sans:ital,wght@0,400;0,600;0,700;1,600&display=swap">
<style>
  :root {
    --brand-red: #f4062f;
    --brand-cyan: #22d8fb;
    --ink: #111111;
    --paper: #ffffff;
    --backdrop: #e9e6e2;
  }
  * { box-sizing: border-box; margin: 0; padding: 0; }
  html, body { width: 1200px; height: 900px; overflow: hidden; }
  body {
    position: relative;
    background: var(--backdrop);
    font-family: "Open Sans", Arial, sans-serif;
  }
  .card {
    position: absolute;
    background: var(--paper);
    overflow: hidden;
    box-shadow: 0 4px 14px rgba(0,0,0,0.18);
  }
  .card-bands { position: absolute; inset: 0; width: 100%; height: 100%; }

  /* Front */
  .card-front { left: 78px; top: 34px; width: 587px; height: 364px; }
  .brand-mark {
    position: absolute; left: 0; right: 0; top: 78px;
    display: flex; justify-content: center; align-items: center; gap: 12px;
    color: var(--brand-red); font-weight: 700; font-size: 36px; letter-spacing: -0.5px;
  }
  .brand-dot { width: 14px; height: 14px; border-radius: 50%; background: var(--brand-cyan); }
  .holder {
    position: absolute; right: 315px; top: 261px; text-align: right; color: var(--paper);
  }
  .holder-name { font-size: 20px; font-weight: 700; line-height: 26px; }
  .holder-title { font-size: 16px; line-height: 22px; }
  .contact-list {
    position: absolute; left: 294px; top: 250px; list-style: none; color: var(--paper);
    font-size: 16px; line-height: 21px;
  }
  .contact-list li { display: flex; align-items: center; gap: 10px; }
  .contact-list svg { width: 12px; height: 12px; fill: var(--paper); flex: none; }
  .address {
    position: absolute; left: 103px; top: 328px; color: var(--paper); font-size: 15px;
  }

  /* Back */
  .card-back { left: 388px; top: 505px; width: 567px; height: 352px; }
  .appointment-title {
    position: absolute; left: 0; right: 0; top: 32px; text-align: center;
    color: var(--brand-red); font-size: 19px; font-weight: 600;
  }
  .appointment-field {
    position: absolute; left: 109px; width: 365px; display: flex; align-items: baseline;
    font-size: 14px; font-weight: 700; color: var(--ink);
  }
  .field-label { color: var(--brand-red); margin-right: 4px; }
  .field-line { flex: 1; border-bottom: 2px dotted var(--ink); transform: translateY(-3px); }
  .field-name { top: 74px; }
  .field-date { top: 117px; }
  .field-time { top: 160px; }
  .field-unit { margin: 0 2px; font-weight: 600; font-size: 15px; }
  .notice {
    position: absolute; left: 0; right: 0; top: 240px; text-align: center;
    color: var(--paper); font-size: 17px; font-style: italic; font-weight: 600;
  }
  .brand-mark-back {
    position: absolute; left: 0; right: 0; top: 282px; text-align: center;
    color: var(--paper); font-weight: 700; font-size: 26px; letter-spacing: -0.5px;
  }
</style>
</head>
<body>

<section class="card card-front" aria-label="Business card front">
  <svg class="card-bands" viewBox="0 0 587 364" preserveAspectRatio="none" aria-hidden="true">
    <polygon points="0,200 402,200 378,226 0,226" fill="var(--brand-cyan)"/>
    <polygon points="412,191 587,191 587,364 0,364 0,229 384,229" fill="var(--brand-red)"/>
  </svg>
  <div class="brand-mark"><span>Brightturn Weightloss</span><span class="brand-dot"></span></div>
  <div class="holder">
    <p class="holder-name">Daniel Hart</p>
    <p class="holder-title">Managing Director</p>
  </div>
  <ul class="contact-list">
    <li><svg viewBox="0 0 24 24"><path d="M6.6 10.8a15 15 0 0 0 6.6 6.6l2.2-2.2c.3-.3.7-.4 1-.2 1.1.4 2.3.6 3.6.6.6 0 1 .4 1 1V20c0 .6-.4 1-1 1C10.6 21 3 13.4 3 4c0-.6.4-1 1-1h3.5c.6 0 1 .4 1 1 0 1.3.2 2.5.6 3.6.1.3 0 .7-.2 1z"/></svg>044-555 010 234</li>
    <li><svg viewBox="0 0 24 24"><path d="M2 5h20v14H2z M2 5l10 8 10-8" fill="var(--paper)"/><path d="M3 6l9 7 9-7" fill="none" stroke="var(--brand-red)" stroke-width="2"/></svg>info@brightturn.com</li>
    <li><svg viewBox="0 0 24 24"><circle cx="12" cy="12" r="10"/><path d="M2 12h20M12 2c3 3 3 17 0 20M12 2c-3 3-3 17 0 20" fill="none" stroke="var(--brand-red)" stroke-width="1.6"/></svg>www.brightturnwellness.com</li>
  </ul>
  <p class="address">12345, Address Goes Here Country Name, 123456.</p>
</section>

<section class="card card-back" aria-label="Appointment card back">
  <svg class="card-bands" viewBox="0 0 567 352" preserveAspectRatio="none" aria-hidden="true">
    <polygon points="0,198 352,198 330,223 0,223" fill="var(--brand-cyan)"/>
    <polygon points="362,190 567,190 567,352 0,352 0,226 336,226" fill="var(--brand-red)"/>
  </svg>
  <h2 class="appointment-title">YOUR NEXT APPOINTMENT IS</h2>
  <div class="appointment-field field-name"><span class="field-label">Name:</span><span class="field-line"></span></div>
  <div class="appointment-field field-date"><span class="field-label">Date:</span><span class="field-line"></span></div>
  <div class="appointment-field field-time"><span class="field-label">Time:</span><span class="field-line"></span><span class="field-unit">AM</span><span class="field-line"></span><span class="field-unit">PM</span></div>
  <p class="notice">If unable to keep appointment,&nbsp; kindly give 24hrs notice.</p>
  <p class="brand-mark-back">Brightturn Weightloss</p>
</section>

</body>
</html>
```